Fitness Equipment & Service

I want to make the card eye catching and fun. We are called Corvane Motion Limited and we are based in Wales. We sell, install and service all types of fitness equipment from Skipping ropes, right through the Dumbbells, Kettle bells and Barbells through to state of the art Treadmills, Running Machines and Strength Equipment. We also design and install changing room furniture and lockers.

TYPOGRAPHY
We would like to use Futrura. Futura has an appearance of efficiency and forwardness. The typeface is derived
from simple geometric forms (near-perfect circles, triangles and squares) and is based on strokes of
near-even weight, which are low in contrast. This is most visible in the almost perfectly round stroke of
the o, which is nonetheless slightly ovoid.
The lowercase has tall ascenders, which rise above the cap line. The uppercase
characters present proportions similar to those of classical Roman capitals.

TYPOGRAPHIC CONSIDERATIONS
No Strike though
No Horizontal Scaling
No Drop Shadows
No Effects
Never use less than 120% Leading

OUR CORPORATE COLOURS
BRAND GUIDELINES
We were thinking that our primary colour palette consists of the Acid Green (Pantone 382) and Process Black.

We work closely with tquarly Ltd and would like to include their name on the card somewhere. I have attached images of the other brands that we work with as an idea or the small icons I have included that illustrate what we do?. I have very kindly been given permission to use any of the images off the files that I have included below, so I hope these help. I will include these below. I would be open to suggestions if it made the card more striking Can you do it?
Updates

Hi All, Just wanted to add a few thoughts but you are the guys with the creative visions (thats why are here) We are based in Wales, UK and we would be open to lots of different ideas on a theme but must be eye catching, Bold and FUN. If you can or think that the Welsh or any dragon could be put in there then go for it (its not a must have) We have also added some ideas for colour but again its over to you!! GO FOR IT ! Thanks and look forward to your visions! Owen

Hi All, Just thought I would sen through the contact details that need to be on the card. (if you want to play around with icons instead of the wording twitter, Facebook, go for it): Corvane Motion Limited Owen Pritchard Managing Director Mob: +44 (0)7582 913 406 e-mail: sales@corvanemotion.co.uk Web: Corvanemotion.co.uk twitter: @motionLetterbin Facebook: Corvane Motion Limited

```html
<!DOCTYPE html>
<html lang="en">
<head>
<meta charset="utf-8">
<title>Corvane Motion Limited – Business Card</title>
<link rel="stylesheet" href="https://fonts.googleapis.com/css2?family=Jost:wght@400;500;700&display=swap">
<style>
  :root {
    --backdrop: #d9d8d4;
    --card-white: #f4f4f2;
    --acid-green: #c4d600;
    --black: #111111;
    --ink: #1c1c1c;
    --ink-soft: #555555;
    --rule: #cfcfc8;
  }
  * { box-sizing: border-box; margin: 0; padding: 0; }
  html, body {
    width: 1200px; height: 844px; overflow: hidden;
    background: var(--backdrop);
    font-family: "Jost", "Futura", Arial, sans-serif;
  }
  .canvas {
    width: 1200px; height: 844px;
    display: flex; align-items: center; justify-content: center; gap: 40px;
  }
  .card {
    width: 520px; height: 298px; position: relative; overflow: hidden;
    box-shadow: 0 6px 18px rgba(0,0,0,.2);
  }

  /* front */
  .card-front { background: var(--card-white); display: flex; }
  .edge-band {
    position: absolute; left: 0; top: 0; bottom: 0; width: 14px;
    background: var(--acid-green);
  }
  .brand-block {
    width: 230px; padding-left: 14px; display: flex; flex-direction: column;
    align-items: center; justify-content: center; gap: 14px;
  }
  .brand-dot { width: 92px; height: 92px; border-radius: 50%; background: var(--acid-green); }
  .brand-name {
    font-size: 17px; font-weight: 700; color: var(--black);
    text-transform: uppercase; letter-spacing: .05em; line-height: 1.25;
    text-align: center; width: 180px;
  }
  .divider { width: 2px; margin: 40px 0; background: var(--acid-green); }
  .details { padding: 40px 0 0 24px; color: var(--ink); }
  .person-name { font-size: 21px; font-weight: 700; color: var(--black); line-height: 1.25; }
  .person-role {
    font-size: 12px; font-weight: 500; line-height: 1.4; color: var(--ink-soft);
    text-transform: uppercase; letter-spacing: .08em; margin-bottom: 18px;
  }
  .contact-list { list-style: none; }
  .contact-list li {
    display: flex; align-items: center; gap: 9px;
    font-size: 13px; line-height: 1.5;
  }
  .contact-icon {
    width: 16px; height: 16px; flex: none; border-radius: 50%;
    background: var(--black); display: flex; align-items: center; justify-content: center;
  }
  .contact-icon svg { width: 8px; height: 8px; fill: var(--acid-green); }
  .partner-line {
    margin-top: 14px; font-size: 11px; font-weight: 500; line-height: 1.4;
    color: var(--ink-soft); text-transform: uppercase; letter-spacing: .08em;
  }

  /* back */
  .card-back {
    background: var(--black);
    display: flex; align-items: center; justify-content: center; gap: 18px;
  }
  .back-dot { width: 64px; height: 64px; border-radius: 50%; background: var(--acid-green); flex: none; }
  .back-name {
    color: var(--acid-green); font-size: 30px; font-weight: 700;
    text-transform: uppercase; letter-spacing: .04em; line-height: 1.2;
    width: 260px;
  }
  .back-band {
    position: absolute; left: 0; right: 0; bottom: 0; height: 14px;
    background: var(--acid-green);
  }
</style>
</head>
<body>
<main class="canvas">
  <section class="card card-front" aria-label="Card front">
    <div class="edge-band"></div>
    <div class="brand-block">
      <div class="brand-dot"></div>
      <p class="brand-name">Corvane Motion Limited</p>
    </div>
    <div class="divider"></div>
    <div class="details">
      <h1 class="person-name">Owen Pritchard</h1>
      <p class="person-role">Managing Director</p>
      <ul class="contact-list">
        <li><span class="contact-icon"><svg viewBox="0 0 10 10" aria-hidden="true"><path d="M2 0.5 L3.6 0.5 L4.2 2.8 L3.1 3.6 Q4 5.8 6.4 6.9 L7.2 5.8 L9.5 6.4 L9.5 8 Q9.5 9.5 8 9.5 Q1.5 9 0.5 2 Q0.5 0.5 2 0.5Z"/></svg></span>+44 (0)7582 913 406</li>
        <li><span class="contact-icon"><svg viewBox="0 0 10 10" aria-hidden="true"><rect x="0.5" y="2" width="9" height="6.5"/></svg></span>sales@corvanemotion.co.uk</li>
        <li><span class="contact-icon"><svg viewBox="0 0 10 10" aria-hidden="true"><circle cx="5" cy="5" r="4.5"/></svg></span>Corvanemotion.co.uk</li>
        <li><span class="contact-icon"><svg viewBox="0 0 10 10" aria-hidden="true"><rect x="1" y="1" width="8" height="8"/></svg></span>@motionLetterbin</li>
        <li><span class="contact-icon"><svg viewBox="0 0 10 10" aria-hidden="true"><rect x="1" y="1" width="8" height="8"/></svg></span>Corvane Motion Limited</li>
      </ul>
      <p class="partner-line">In partnership with tquarly Ltd</p>
    </div>
  </section>
  <section class="card card-back" aria-label="Card back">
    <div class="back-dot"></div>
    <p class="back-name">Corvane Motion Limited</p>
    <div class="back-band"></div>
  </section>
</main>
</body>
</html>
```